Northvale Strategy Partners Website Design

I need a website design for my new business consulting and executive coaching firm, Northvale Strategy Partners. We provide consultative services to business C-suites as well as personal coaching to executives. I have attached the logo with color scheme I have chosen. I would like the website to reflect professionalism and continue the color scheme in the logo.

Target Market(s)

Small to medium business and their executives; middle to upper income men and women in mid- to late career looking for significance

Industry/Entity Type

Business Consultant

Number of Pages Required

4 page

Requirements
Must have
• A homepage with prominent logo and way to contact for more information; an area on the homepage with easy to read, clear text to describe what the company does; a prominent area on the homepage for a tagline; a blog page that can be updated regularly, an "about us" page with biographical information; an "about us" page; a page detailing services offered
• The web design must match the logo colors and font that I have uploaded.
Nice to have
• A lighthouse picture in the background or header
Should not have
• A lot of text area on the homepage

```html
<!DOCTYPE html>
<html lang="en">
<head>
<meta charset="utf-8">
<title>Northvale Strategy Partners</title>
<link rel="stylesheet" href="https://fonts.googleapis.com/css2?family=Roboto+Slab:wght@400&family=Roboto+Condensed:wght@400&family=Roboto:wght@400;500&display=swap">
<style>
  :root {
    --navy: #1d2f66;
    --maroon: #6f1013;
    --nav-red: #7a1416;
    --ink: #111111;
    --card: rgba(232, 226, 232, 0.55);
    --grey-btn: #6c6c6c;
    --white: #ffffff;
    --sky-top: #a14fa5;
    --sky-mid: #d9688c;
    --sky-low: #ee9262;
    --sky-base: #c8704a;
  }
  * { box-sizing: border-box; margin: 0; padding: 0; }
  html, body { width: 1200px; height: 825px; overflow: hidden; }
  body { position: relative; font-family: "Roboto", Arial, sans-serif; color: var(--ink); }

  .hero-scene {
    position: absolute; inset: 0 0 45px 0;
    background: linear-gradient(180deg, var(--sky-top) 0%, var(--sky-mid) 40%, var(--sky-low) 70%, var(--sky-base) 100%);
  }

  .site-header { position: absolute; top: 0; left: 0; width: 1200px; height: 120px; }
  .brand {
    position: absolute; left: 150px; top: 62px; width: 190px;
    font-family: "Roboto Slab", Georgia, serif; font-size: 19px; line-height: 22px; font-weight: 400;
    color: var(--navy); text-align: center;
  }
  .contact-line {
    position: absolute; left: 879px; top: 20px; display: flex; align-items: center; gap: 14px;
    font-family: "Roboto Condensed", Arial, sans-serif; font-size: 21px; color: var(--ink);
  }
  .main-nav { position: absolute; right: 160px; top: 69px; display: flex; gap: 19px; }
  .main-nav a {
    font-family: "Roboto Slab", Georgia, serif; font-size: 15px; font-weight: 400; color: var(--nav-red);
    text-decoration: none; padding: 3px 13px; line-height: 17px;
  }
  .main-nav a.is-current { background: var(--navy); color: var(--white); }

  .tagline {
    position: absolute; left: 223px; top: 310px; width: 760px;
    font-family: "Roboto Slab", Georgia, serif; font-size: 33px; line-height: 37px; font-weight: 400;
    color: var(--navy); display: flex; gap: 17px;
  }
  .tagline-lead { white-space: nowrap; flex-shrink: 0; }
  .tagline-rest { width: 530px; }

  .feature { position: absolute; top: 588px; width: 273px; height: 192px; background: var(--card); text-align: center; }
  .feature--about { left: 160px; }
  .feature--services { left: 464px; }
  .feature--inquiry { left: 768px; }
  .feature-badge {
    position: absolute; left: 77px; top: -78px; width: 120px; height: 120px; border-radius: 50%;
    background: var(--navy); border: 4px solid #d7d3dc; display: flex; align-items: center; justify-content: center;
  }
  .feature--about .feature-badge { background: var(--maroon); border-color: var(--navy); }
  .feature-title {
    margin-top: 53px; font-family: "Roboto Condensed", Arial, sans-serif; font-size: 21px; font-weight: 400;
    line-height: 24px; color: var(--ink);
  }
  .feature-text { margin: 6px auto 0; width: 245px; font-size: 12px; line-height: 18.5px; color: var(--ink); }
  .arrow-button {
    display: inline-block; margin-top: 8px; padding: 0 26px 0 9px; height: 32px; line-height: 32px;
    font-size: 14px; font-weight: 400; color: var(--white); background: var(--grey-btn); text-decoration: none;
    clip-path: polygon(0 0, calc(100% - 16px) 0, 100% 50%, calc(100% - 16px) 100%, 0 100%);
  }
  .arrow-button--primary { background: var(--navy); }

  .site-footer {
    position: absolute; left: 0; bottom: 0; width: 1200px; height: 45px; background: var(--maroon);
    color: var(--white);
  }
  .social { position: absolute; left: 175px; top: 8px; display: flex; align-items: center; gap: 7px;
    font-family: "Roboto Condensed", Arial, sans-serif; font-size: 15px; }
  .social-label { margin-right: 4px; }
  .social-dot { width: 29px; height: 29px; border-radius: 50%; background: var(--white); display: inline-block; }
  .copyright { position: absolute; right: 162px; top: 15px; font-size: 12px; }
</style>
</head>
<body>
  <div class="hero-scene" role="img" aria-label="Lighthouse on a rocky shore with its beam across a purple and orange sunset over the sea"></div>

  <header class="site-header">
    <div class="brand">Northvale Strategy Partners</div>
    <div class="contact-line">
      <svg width="30" height="30" viewBox="0 0 30 30" aria-hidden="true">
        <circle cx="15" cy="15" r="13.5" fill="none" stroke="#1d2f66" stroke-width="2"/>
        <path d="M11 8.5c1 0 1.6 2.7 1.6 3.6 0 .8-1.4 1.2-1.2 2 .5 2 1.6 3.7 3.3 4.9.6.4 1.4-1 2.2-.8.9.2 3 1.6 2.7 2.5-.5 1.3-1.8 2.4-3.1 2-4.3-1.3-7.6-5.3-8-9.6-.2-2.1 1.2-4.6 2.5-4.6z" fill="#1d2f66"/>
      </svg>
      <span>555-014-2280</span>
    </div>
    <nav class="main-nav">
      <a href="#" class="is-current">HOME</a>
      <a href="#">ABOUT US</a>
      <a href="#">SERVICES</a>
      <a href="#">BLOG</a>
      <a href="#">CONTACT US</a>
    </nav>
  </header>

  <h1 class="tagline"><span class="tagline-lead">We Are A Firm</span><span class="tagline-rest">Providing Business Consulting And Executive Coaching</span></h1>

  <section class="feature feature--about">
    <div class="feature-badge"></div>
    <h2 class="feature-title">About Us</h2>
    <p class="feature-text">Lorem ipsum dolor sit amet, consectetuer into euismod tincidunt ut laoreet dolore magnain aliquam erat volutpat.</p>
    <a href="#" class="arrow-button arrow-button--primary">READ MORE</a>
  </section>

  <section class="feature feature--services">
    <div class="feature-badge">
      <svg width="56" height="60" viewBox="0 0 56 60" aria-hidden="true">
        <rect x="6" y="3" width="44" height="30" rx="2" fill="none" stroke="#fff" stroke-width="2.5"/>
        <rect x="30" y="18" width="4" height="10" fill="#fff"/>
        <rect x="36" y="13" width="4" height="15" fill="#fff"/>
        <rect x="42" y="9" width="4" height="19" fill="#fff"/>
        <circle cx="12" cy="46" r="4" fill="#fff"/><rect x="6" y="51" width="12" height="7" rx="3" fill="#fff"/>
        <circle cx="28" cy="46" r="4" fill="#fff"/><rect x="22" y="51" width="12" height="7" rx="3" fill="#fff"/>
        <circle cx="44" cy="46" r="4" fill="#fff"/><rect x="38" y="51" width="12" height="7" rx="3" fill="#fff"/>
      </svg>
    </div>
    <h2 class="feature-title">Services We Provide</h2>
    <p class="feature-text">Lorem ipsum dolor sit amet, consectetuer into euismod tincidunt ut laoreet dolore magnain aliquam erat volutpat.</p>
    <a href="#" class="arrow-button">READ MORE</a>
  </section>

  <section class="feature feature--inquiry">
    <div class="feature-badge">
      <svg width="56" height="56" viewBox="0 0 30 30" aria-hidden="true">
        <circle cx="15" cy="15" r="13.5" fill="none" stroke="#fff" stroke-width="1.6"/>
        <path d="M11 8.5c1 0 1.6 2.7 1.6 3.6 0 .8-1.4 1.2-1.2 2 .5 2 1.6 3.7 3.3 4.9.6.4 1.4-1 2.2-.8.9.2 3 1.6 2.7 2.5-.5 1.3-1.8 2.4-3.1 2-4.3-1.3-7.6-5.3-8-9.6-.2-2.1 1.2-4.6 2.5-4.6z" fill="#fff"/>
      </svg>
    </div>
    <h2 class="feature-title">QUICK INQUIRY</h2>
    <p class="feature-text">Lorem ipsum dolor sit amet, consectetuer into euismod tincidunt ut laoreet dolore magnain aliquam erat volutpat.</p>
    <a href="#" class="arrow-button">GET STARTED</a>
  </section>

  <footer class="site-footer">
    <div class="social">
      <span class="social-label">FOLLOW US</span>
      <span class="social-dot"></span>
      <span class="social-dot"></span>
      <span class="social-dot"></span>
      <span class="social-dot"></span>
    </div>
    <p class="copyright">© 2016 Northvale Strategy Partners All Rights Reserved</p>
  </footer>
</body>
</html>
```